Velk Partners Building Business Cards

We need a business card that reflects our business as "Solar Experts" in San Diego. Browse our website www.velkpartners.example our License needs to be displayed as "CSLB# 3867140" our phone number is (619) 555-0187

Save thousands on your electric bills and increase the value of your home while helping to protect the environment. Our solar installation experts will help you design the system that's right for you, using only the highest quality equipment that will look great and give you ideal performance. Our goal is to make you energy independent, and get your electric bill to 0.

Paul Osterby
(619) 555-0187
paul@velkpartners.example

Target Market(s)

Home owners in san diego looking for solar

Industry/Entity Type

Solar Energy

Contact Information for Business Card

Paul Osterby
(619) 555-0187
paul@velkpartners.example

Font styles to use
Other font styles liked:
• Use our logo font

Requirements
Must have
• License needs to be displayed as "CSLB# 3867140" our phone number is (619) 555-0187
Nice to have
• Real images of rooftop home solar in san diego
Should not have
• our business address

```html
<!DOCTYPE html>
<html lang="en">
<head>
<meta charset="utf-8">
<title>Velk Partners Building – Business Card</title>
<link rel="stylesheet" href="https://fonts.googleapis.com/css2?family=Open+Sans:wght@400;600;700&display=swap">
<style>
  :root {
    --navy: #1c4587;
    --sun: #f8b334;
    --ink: #333a44;
    --paper: #ffffff;
    --backdrop: #e7e6e3;
  }
  html, body {
    margin: 0;
    padding: 0;
    width: 1200px;
    height: 1000px;
    overflow: hidden;
    background: var(--backdrop);
    font-family: "Open Sans", Arial, sans-serif;
  }
  .stage { position: relative; width: 1200px; height: 1000px; }
  .card {
    position: absolute;
    left: 316px;
    width: 560px;
    height: 320px;
    background: var(--paper);
    border-radius: 22px;
    overflow: hidden;
    box-shadow: 0 3px 8px rgba(0,0,0,0.25);
  }
  .card--front { top: 172px; }
  .card--back { top: 536px; }

  .brand {
    position: absolute;
    display: flex;
    align-items: center;
    gap: 10px;
    color: var(--navy);
    font-weight: 700;
    font-size: 27px;
    letter-spacing: -0.5px;
    white-space: nowrap;
  }
  .brand__dot {
    width: 16px; height: 16px; border-radius: 50%;
    background: var(--navy);
    flex: none;
  }
  .card--front .brand { left: 20px; top: 30px; }
  .card--back .brand {
    left: 200px;
    width: 340px;
    top: 218px;
    justify-content: center;
    font-size: 23px;
    gap: 8px;
  }
  .card--back .brand__dot { width: 14px; height: 14px; }

  .sun-art {
    position: absolute;
    left: 0;
    top: 110px;
    width: 168px;
    height: 210px;
    border-top-right-radius: 100% 70%;
    background: linear-gradient(180deg, var(--sun) 0%, var(--sun) 55%, var(--navy) 85%, var(--navy) 100%);
    opacity: 0.9;
  }

  .contact {
    position: absolute;
    left: 14px;
    top: 148px;
    margin: 0;
    padding: 0;
    list-style: none;
    color: var(--ink);
    font-size: 14.5px;
    line-height: 22px;
  }
  .contact li { display: flex; align-items: center; gap: 9px; }
  .contact svg { width: 15px; height: 15px; fill: var(--navy); }

  .person {
    position: absolute;
    right: 24px;
    top: 146px;
    margin: 0;
    font-size: 28px;
    font-weight: 600;
    letter-spacing: 0.5px;
    color: var(--navy);
    white-space: nowrap;
  }
  .person__last { color: var(--sun); }
  .edge-tab {
    position: absolute;
    right: 0; top: 148px;
    width: 10px; height: 32px;
    background: var(--navy);
    border-radius: 4px 0 0 4px;
  }

  .wave { position: absolute; left: 0; bottom: 0; width: 560px; height: 320px; }

  .footer-info {
    position: absolute;
    right: 24px;
    bottom: 20px;
    text-align: right;
    font-size: 12.5px;
    line-height: 20px;
    font-weight: 600;
    color: #ffffff;
  }
  .footer-info__web { color: var(--sun); }
  .footer-info__web span { color: #ffffff; }

  .back-web {
    position: absolute;
    left: 200px;
    width: 340px;
    top: 282px;
    text-align: center;
    color: var(--navy);
    font-size: 14.5px;
  }
</style>
</head>
<body>
<main class="stage">

  <section class="card card--front" aria-label="Business card front">
    <svg class="wave" viewBox="0 0 560 320" aria-hidden="true">
      <path d="M0,245 C70,275 160,296 245,293 C150,286 70,268 0,252 Z" fill="var(--sun)"/>
      <path d="M0,258 C80,292 200,302 290,282 C380,262 460,218 560,222 L560,320 L0,320 Z" fill="var(--navy)"/>
    </svg>

    <div class="brand"><span class="brand__dot"></span>Velk Partners Building</div>

    <ul class="contact">
      <li>
        <svg viewBox="0 0 24 24" aria-hidden="true"><path d="M6.6 10.8c1.4 2.8 3.8 5.1 6.6 6.6l2.2-2.2c.3-.3.7-.4 1-.2 1.1.4 2.3.6 3.6.6.6 0 1 .4 1 1V20c0 .6-.4 1-1 1C10.6 21 3 13.4 3 4c0-.6.4-1 1-1h3.5c.6 0 1 .4 1 1 0 1.3.2 2.5.6 3.6.1.3 0 .7-.2 1z"/></svg>
        (619) 555-0187
      </li>
      <li>
        <svg viewBox="0 0 24 24" aria-hidden="true"><path d="M3 5h18v14H3zM5 7v.5l7 5 7-5V7zm0 2.9V17h14V9.9l-7 5z"/></svg>
        paul@velkpartners.example
      </li>
    </ul>

    <h1 class="person">PAUL <span class="person__last">OSTERBY</span></h1>
    <div class="edge-tab"></div>

    <div class="footer-info">
      <div>License-"CSLB# 3867140"</div>
      <div class="footer-info__web">www.velkpartners<span>.example</span></div>
    </div>
  </section>

  <section class="card card--back" aria-label="Business card back">
    <div class="sun-art" role="img" aria-label="Illustration of a rising sun over ocean waves in the lower left corner"></div>
    <div class="brand"><span class="brand__dot"></span>Velk Partners Building</div>
    <div class="back-web">www.velkpartners.example</div>
  </section>

</main>
</body>
</html>
```